Landing Page / Waitlist

I would like a landing page for people to sign up for a waiting list. The text on the page should include (but is not limited to):
1) Main point: The accounting system you'll love
2) Secondary points:
a. Ruthlessly efficient
b. Quietly intelligent
c. Driven by AI
I've attached a file of our logo

The design should be simple, clean, and innovative - this is an ai company

```html
<!DOCTYPE html>
<html lang="en">
<head>
<meta charset="utf-8">
<title>LedgerNorth – Waitlist Landing Concepts</title>
<link href="https://fonts.googleapis.com/css2?family=Inter:wght@300;400;500;600;700;800&display=swap" rel="stylesheet">
<style>
  :root {
    --board: #fafafa;
    --frame: #ffffff;
    --ink-white: #ffffff;
    --wordmark: #8a8d93;
    --brand-blue: #0a9fe6;
    --brand-blue-bright: #05b2f5;
    --night: #050608;
    --night-soft: #16191f;
    --navy: #050a3c;
    --navy-deep: #03072b;
    --navy-circle: #0a1550;
    --tile-bg: rgba(30, 32, 36, 0.9);
    --tile-line: rgba(255, 255, 255, 0.35);
    --icon-grey: #b9bcc2;
  }
  * { box-sizing: border-box; margin: 0; padding: 0; }
  html, body {
    width: 911px; height: 1200px; overflow: hidden;
    background: var(--board);
    font-family: "Inter", Arial, sans-serif;
  }
  .board { position: relative; width: 911px; height: 1200px; }

  .concept {
    position: absolute; left: 71px; width: 769px; height: 504px;
    background: var(--frame);
    padding: 2px;
    box-shadow: 0 6px 22px rgba(0,0,0,0.12);
  }
  .concept--dark { top: 65px; }
  .concept--navy { top: 629px; }
  .screen { position: relative; width: 765px; height: 500px; overflow: hidden; color: var(--ink-white); }

  /* shared brand lockup */
  .brand { position: absolute; left: 0; right: 0; display: flex; flex-direction: column; align-items: center; }
  .brand-mark { background: var(--brand-blue); }
  .brand-name { color: var(--wordmark); font-weight: 600; letter-spacing: -0.02em; line-height: 1; }

  .copyright { position: absolute; left: 0; right: 0; top: 456px; text-align: center; font-size: 11px; font-weight: 400; }

  /* concept one */
  .concept--dark .screen { background: var(--night); }
  .particle-field {
    position: absolute; inset: 0;
    background:
      radial-gradient(ellipse 45% 30% at 30% 35%, rgba(70,74,82,0.35), transparent 70%),
      radial-gradient(ellipse 50% 28% at 70% 60%, rgba(60,64,72,0.3), transparent 70%),
      radial-gradient(ellipse 40% 25% at 85% 20%, rgba(55,58,66,0.3), transparent 70%),
      linear-gradient(180deg, var(--night) 0%, var(--night-soft) 55%, var(--night) 100%);
  }
  .concept--dark .brand { top: 66px; }
  .concept--dark .brand-mark { width: 44px; height: 44px; margin-bottom: 18px; }
  .concept--dark .brand-name { font-size: 33px; }
  .hero-title { position: absolute; left: 0; right: 0; top: 192px; text-align: center; font-size: 35px; line-height: 1.2; }
  .hero-title strong { font-weight: 800; }
  .hero-title span { font-weight: 300; }

  .feature-row { position: absolute; top: 254px; left: 156px; display: flex; gap: 22px; }
  .feature-tile {
    width: 137px; height: 68px; border: 1px solid var(--tile-line); border-radius: 4px;
    background: var(--tile-bg); display: flex; align-items: center; gap: 9px; padding-left: 13px;
    box-shadow: inset 0 1px 0 rgba(255,255,255,0.08), 0 3px 8px rgba(0,0,0,0.6);
  }
  .feature-tile svg { width: 32px; height: 32px; flex: none; }
  .feature-text { font-size: 13px; line-height: 1.5; }
  .feature-text b { display: block; font-weight: 700; }
  .feature-text span { font-weight: 400; }

  .waitlist-bar {
    position: absolute; top: 347px; left: 137px; width: 492px; height: 46px;
    border: 1px solid var(--ink-white); border-radius: 3px;
  }
  .waitlist-bar .email-label { position: absolute; left: 13px; top: 12px; font-size: 13px; }
  .waitlist-bar .join-button {
    position: absolute; right: 7px; top: 7px; width: 127px; height: 31px;
    background: var(--brand-blue); color: var(--ink-white); border-radius: 2px;
    font-size: 13px; font-weight: 600; display: flex; align-items: center; justify-content: center;
  }

  /* concept two */
  .concept--navy .screen { background: var(--navy); }
  .navy-circle { position: absolute; border-radius: 50%; background: var(--navy-circle); opacity: 0.6; }
  .navy-circle--top { width: 180px; height: 180px; left: -95px; top: -100px; }
  .navy-circle--mid { width: 66px; height: 66px; left: 265px; top: 212px; opacity: 0.5; }
  .navy-circle--low { width: 170px; height: 170px; left: 45px; top: 457px; }
  .chip-visual {
    position: absolute; left: 400px; top: 74px; width: 333px; height: 378px;
    background: radial-gradient(circle at 50% 55%, #e8f6ff 0%, #37a8ff 10%, #0f56c9 28%, rgba(8,30,110,0.6) 50%, transparent 72%);
  }
  .concept--navy .brand { top: 27px; }
  .concept--navy .brand-mark { width: 34px; height: 34px; margin-bottom: 10px; }
  .concept--navy .brand-name { font-size: 27px; }
  .pitch { position: absolute; left: 48px; top: 146px; }
  .pitch h1 { font-size: 31px; line-height: 1.22; }
  .pitch h1 strong { font-weight: 700; display: block; }
  .pitch h1 span { font-weight: 400; display: block; }
  .pitch-rule { width: 79px; height: 2px; background: var(--brand-blue-bright); margin-top: 10px; margin-left: 3px; }
  .pitch-list { list-style: none; margin-top: 15px; margin-left: 4px; }
  .pitch-list li { display: flex; align-items: center; gap: 10px; font-size: 14px; font-weight: 500; height: 27.5px; }
  .pitch-list li::before { content: ""; width: 9px; height: 9px; background: var(--brand-blue-bright); }
  .signup { position: absolute; left: 50px; top: 336px; display: flex; gap: 8px; }
  .signup .email-field {
    width: 210px; height: 35px; background: var(--ink-white); color: #333;
    font-size: 11px; padding-left: 10px; display: flex; align-items: center;
  }
  .signup .join-button {
    width: 123px; height: 35px; background: var(--brand-blue-bright); color: var(--ink-white);
    font-size: 12.5px; font-weight: 600; display: flex; align-items: center; justify-content: center;
  }
</style>
</head>
<body>
<div class="board">

  <section class="concept concept--dark">
    <div class="screen">
      <div class="particle-field" role="img" aria-label="Dark abstract background of flowing digital particle waves"></div>

      <div class="brand">
        <div class="brand-mark"></div>
        <div class="brand-name">LedgerNorth</div>
      </div>

      <h1 class="hero-title"><strong>The Accounting System</strong> <span>You'll Love</span></h1>

      <div class="feature-row">
        <div class="feature-tile">
          <svg viewBox="0 0 32 32" aria-hidden="true">
            <circle cx="16" cy="16" r="10" fill="none" stroke="var(--icon-grey)" stroke-width="5" stroke-dasharray="4 2.3"/>
            <circle cx="16" cy="16" r="6" fill="none" stroke="var(--icon-grey)" stroke-width="3"/>
          </svg>
          <div class="feature-text"><b>Ruthlessly</b><span>Efficient</span></div>
        </div>
        <div class="feature-tile">
          <svg viewBox="0 0 32 32" aria-hidden="true">
            <path d="M15 5a6 6 0 0 0-6 3 5 5 0 0 0-4 6 5 5 0 0 0 1 7 5 5 0 0 0 5 5 4 4 0 0 0 4 2z" fill="var(--icon-grey)"/>
            <g stroke="var(--icon-grey)" stroke-width="1.6" fill="var(--icon-grey)">
              <line x1="17" y1="9" x2="24" y2="9"/><circle cx="26" cy="9" r="1.8"/>
              <line x1="17" y1="16" x2="27" y2="16"/><circle cx="29" cy="16" r="1.8"/>
              <line x1="17" y1="23" x2="24" y2="23"/><circle cx="26" cy="23" r="1.8"/>
            </g>
          </svg>
          <div class="feature-text"><b>Quietly</b><span>Intelligent</span></div>
        </div>
        <div class="feature-tile" style="padding-left:26px">
          <svg viewBox="0 0 32 32" aria-hidden="true">
            <rect x="5" y="5" width="22" height="22" rx="4" fill="var(--icon-grey)"/>
            <g stroke="var(--icon-grey)" stroke-width="1.5">
              <line x1="10" y1="1" x2="10" y2="5"/><line x1="16" y1="1" x2="16" y2="5"/><line x1="22" y1="1" x2="22" y2="5"/>
              <line x1="10" y1="27" x2="10" y2="31"/><line x1="16" y1="27" x2="16" y2="31"/><line x1="22" y1="27" x2="22" y2="31"/>
              <line x1="1" y1="10" x2="5" y2="10"/><line x1="1" y1="16" x2="5" y2="16"/><line x1="1" y1="22" x2="5" y2="22"/>
              <line x1="27" y1="10" x2="31" y2="10"/><line x1="27" y1="16" x2="31" y2="16"/><line x1="27" y1="22" x2="31" y2="22"/>
            </g>
            <path d="M16 9l1.8 5.2L23 16l-5.2 1.8L16 23l-1.8-5.2L9 16l5.2-1.8z" fill="#2a2d33"/>
          </svg>
          <div class="feature-text"><b>Driven</b><span>by AI</span></div>
        </div>
      </div>

      <div class="waitlist-bar">
        <span class="email-label">Email</span>
        <span class="join-button">Join the Waitlist</span>
      </div>

      <p class="copyright">Copyrights@2025.company Name.All Rights Reserved</p>
    </div>
  </section>

  <section class="concept concept--navy">
    <div class="screen">
      <div class="navy-circle navy-circle--top"></div>
      <div class="navy-circle navy-circle--mid"></div>
      <div class="navy-circle navy-circle--low"></div>
      <div class="chip-visual" role="img" aria-label="Glowing blue AI processor chip with radiating circuit lines"></div>

      <div class="brand">
        <div class="brand-mark"></div>
        <div class="brand-name">LedgerNorth</div>
      </div>

      <div class="pitch">
        <h1><strong>The Accounting System</strong><span>You'll Love</span></h1>
        <div class="pitch-rule"></div>
        <ul class="pitch-list">
          <li>Ruthlessly efficient</li>
          <li>Quietly intelligent</li>
          <li>Driven by AI</li>
        </ul>
      </div>

      <div class="signup">
        <span class="email-field">Email</span>
        <span class="join-button">Join The Waitlist</span>
      </div>

      <p class="copyright">Copyrights@2025.company Name.All Rights Reserved</p>
    </div>
  </section>

</div>
</body>
</html>
```